BRIGHT RIVER POWER.

I'd like my business logo.
contact name: Dennis Halvorsen
phone:0438759164
email: info@brightriverpower.net.au
website: www.brightriverpower.net.au

services:
solar
battery storage
LED lighting
energy saving solutions
general electrical
I'd like the design to look professional

Target Market(s)

Everyone

Industry/Entity Type

Business

Contact Information for Business Card

as described above

Requirements
Must have
• Id like the colours and the design to work well with my logo.

```html
<!DOCTYPE html>
<html lang="en">
<head>
<meta charset="utf-8">
<title>Bright River Power – Business Card</title>
<link rel="stylesheet" href="https://fonts.googleapis.com/css2?family=Open+Sans:wght@400;600;700&display=swap">
<style>
  :root {
    --green: #52a43a;
    --green-light: #6cbd45;
    --green-dark: #3f8a2c;
    --yellow: #f7b218;
    --orange: #f39c12;
    --white: #ffffff;
    --stage: #ecebe8;
  }
  * { box-sizing: border-box; margin: 0; padding: 0; }
  html, body {
    width: 1200px; height: 900px; overflow: hidden;
    background: var(--stage);
    font-family: "Open Sans", Arial, sans-serif;
  }
  .card {
    position: absolute; overflow: hidden;
    box-shadow: 0 6px 18px rgba(0,0,0,.18);
  }

  /* Front */
  .card-front {
    left: 78px; top: 33px; width: 588px; height: 365px;
    background: var(--white);
  }
  .card-front .bands { position: absolute; left: 0; top: 0; }
  .brand {
    position: absolute; left: 150px; top: 110px;
    display: flex; align-items: center; gap: 14px;
  }
  .brand-dot {
    width: 34px; height: 34px; border-radius: 50%;
    background: var(--orange);
  }
  .brand-name {
    color: var(--green); font-weight: 700; font-size: 34px;
    letter-spacing: 0.5px;
  }
  .holder-name {
    position: absolute; left: 24px; top: 292px;
    color: var(--white); font-weight: 700; font-size: 22px;
    text-transform: uppercase;
  }
  .contact-list {
    position: absolute; right: 16px; top: 270px;
    list-style: none; text-align: right;
    color: var(--white); font-size: 15px; line-height: 24px;
  }
  .contact-list li { display: flex; align-items: center; justify-content: flex-end; gap: 7px; }
  .contact-list svg { width: 12px; height: 12px; fill: var(--white); }

  /* Back */
  .card-back {
    left: 388px; top: 505px; width: 567px; height: 352px;
    background: var(--green);
  }
  .services {
    position: absolute; left: 40px; top: 120px; width: 250px;
    text-align: center; color: var(--white);
  }
  .services h2 { font-size: 18px; font-weight: 700; margin-bottom: 12px; }
  .services ul { list-style: none; font-size: 15px; line-height: 28px; }
  .brand-circle {
    position: absolute; left: 330px; top: 60px;
    width: 230px; height: 230px; border-radius: 50%;
    background: var(--green-light);
  }
</style>
</head>
<body>

<section class="card card-front" aria-label="Business card front">
  <svg class="bands" width="588" height="365" viewBox="0 0 588 365">
    <polygon points="0,225 362,225 348,246 0,246" fill="var(--yellow)"/>
    <polygon points="0,249 350,249 375,212 588,212 588,365 0,365" fill="var(--green)"/>
  </svg>
  <div class="brand">
    <span class="brand-dot"></span>
    <span class="brand-name">BRIGHT RIVER POWER</span>
  </div>
  <p class="holder-name">Dennis Halvorsen</p>
  <ul class="contact-list">
    <li>0438759164
      <svg viewBox="0 0 24 24"><path d="M6.6 10.8a15 15 0 006.6 6.6l2.2-2.2c.3-.3.7-.4 1-.2 1.1.4 2.3.6 3.6.6.6 0 1 .4 1 1V20c0 .6-.4 1-1 1A17 17 0 013 4c0-.6.4-1 1-1h3.5c.6 0 1 .4 1 1 0 1.3.2 2.5.6 3.6.1.3 0 .7-.2 1z"/></svg>
    </li>
    <li>info@brightriverpower.net.au
      <svg viewBox="0 0 24 24"><path d="M2 5h20v14H2z M2 5l10 8 10-8" stroke="var(--green)" stroke-width="1.5"/></svg>
    </li>
    <li>www.brightriverpower.net.au
      <svg viewBox="0 0 24 24"><circle cx="12" cy="12" r="10"/></svg>
    </li>
  </ul>
</section>

<section class="card card-back" aria-label="Business card back">
  <div class="services">
    <h2>WHAT I DO</h2>
    <ul>
      <li>Solar</li>
      <li>Battery Storage</li>
      <li>LED Lighting</li>
      <li>Energy Saving Solutions</li>
    </ul>
  </div>
  <span class="brand-circle"></span>
</section>

</body>
</html>
```